Suds Haven Laundromat Wordpress Design

We need a Wordpress website design for our laundromat, Suds Haven Atlanta, at www.sudshavenatlanta-example.com. We would like to have 6 pages: Home, About Us, Services, Locations, Reviews and Contact us. We will provide content for the text on each page. What we do: We are a full service laundromat that provides dry cleaning drop off, professional laundry services, wash dry fold and self service laundry to the local community. We would like to use the color scheme from our logo to convey a warm, safe, and bright business that caters to its diverse community.
Updates

I like the structure of this laundromat website: http://www.washtroveusa-example.com/ Using my logo and color scheme in the above referenced website is what. Am looking for. The photos attached to the project with the female model should be used as a primary focus and supplemented by actual photos of the equipment.

Target Market(s)

Our target market is a diverse group of people from Midtown Atlanta - LGBTQ community /Locals/Regulars that have been coming to laundromat for 30 years.

Industry/Entity Type

Laundromat

Coding

Coded - Design and coding required

Number of Pages Required

5+ page

Font styles to use
Sans Serif

Colors
0054AA
0677BA
7BADD7
CADEEF
E8F1F8

Requirements
Must have
• Feature this video on the main page: https://videohost-example.com/xq7Rm2bPz4k

```html
<!DOCTYPE html>
<html lang="en">
<head>
<meta charset="utf-8">
<title>Contact Us – Suds Haven</title>
<link rel="stylesheet" href="https://fonts.googleapis.com/css2?family=Montserrat:wght@400;500;600&family=Oswald:wght@500&family=Roboto:wght@400;500&display=swap">
<style>
:root{
  --navy:#2e4466;
  --blue:#0054aa;
  --mid:#0677ba;
  --cyan:#1aa3df;
  --sky:#7badd7;
  --pale:#cadeef;
  --ice:#e8f1f8;
  --ink:#222;
  --line:#d9dde3;
}
*{box-sizing:border-box;margin:0;padding:0}
html,body{width:1200px;height:2456px;overflow:hidden;background:#fff}
body{position:relative;font-family:"Montserrat",sans-serif;color:var(--ink)}
.abs{position:absolute}

/* header */
.site-header{left:0;top:0;width:1200px;height:76px;background:#fff;z-index:3}
.brand{left:103px;top:18px;display:flex;align-items:center;gap:8px}
.brand-mark{width:14px;height:14px;border-radius:50%;background:var(--cyan)}
.brand-name{font-size:26px;font-weight:600;color:var(--blue);letter-spacing:.5px}
.brand-tag{left:168px;top:62px;font-size:10px;color:var(--cyan);font-weight:500}
.main-nav a{position:absolute;top:34px;font-size:13px;font-weight:500;color:var(--ink);text-decoration:none}
.main-nav .active::after{content:"";position:absolute;left:0;right:0;top:38px;height:4px;background:var(--blue)}
.nav-divider{left:1029px;top:19px;width:2px;height:38px;background:var(--blue)}
.social-dot{width:12px;height:12px;border-radius:50%;background:var(--ink);top:33px}

/* hero */
.hero{left:0;top:76px;width:1200px;height:600px;overflow:hidden}
.hero-photo{width:100%;height:100%;background:linear-gradient(180deg,#b9d8d2 0%,#d9d6c7 35%,#bdb7a8 65%,#8f8878 100%)}
.hero svg{position:absolute;left:0;top:0}

.breadcrumb{left:163px;top:698px;font-size:13px;font-weight:500}
.breadcrumb span{color:var(--blue);font-weight:600}

.section-title{left:0;width:1200px;top:790px;text-align:center;font-family:"Oswald",sans-serif;font-size:32px;font-weight:500;color:#333;letter-spacing:.5px}
.section-title b{color:var(--blue);font-weight:500}
.title-rule{left:578px;top:834px;width:44px;height:3px;background:var(--cyan)}

/* contact panel */
.contact-panel{left:161px;top:935px;width:428px;height:373px;background:var(--navy);color:#fff;font-size:14px;line-height:24px}
.contact-row{position:absolute;left:88px}
.contact-row svg{position:absolute;left:-45px;top:0}

/* map */
.map{left:589px;top:877px;width:611px;height:490px;background:linear-gradient(135deg,#e6ece9 0%,#dfe7e2 40%,#cfe3cf 70%,#e8ebed 100%)}
.map-card{left:598px;top:884px;width:322px;height:172px;background:#fff;box-shadow:0 1px 4px rgba(0,0,0,.25);font-family:"Roboto",sans-serif;padding:14px 18px}
.map-card h3{font-size:21px;font-weight:500;color:#222;margin-bottom:10px}
.map-card p{font-size:17px;color:#555;line-height:21px}
.map-card .rating{margin-top:8px;color:#555;font-size:19px}
.map-card .rating i{font-style:normal;color:#e7711b;font-size:17px;margin:0 14px 0 4px}
.map-card .rating a,.map-card .more{color:#1a73e8;font-size:17px;text-decoration:none}
.map-card .more{display:block;margin-top:12px;font-size:18px}
.map-zoom{left:1138px;top:1232px;width:60px;height:120px;background:#fff;box-shadow:0 1px 4px rgba(0,0,0,.3)}
.map-zoom::before,.map-zoom::after{content:"";position:absolute;left:18px;width:26px;height:3px;background:#666}
.map-zoom::before{top:29px}.map-zoom::after{top:89px}
.map-zoom i{position:absolute;left:30px;top:17px;width:3px;height:26px;background:#666}

/* form */
.intro{left:0;width:1200px;text-align:center;font-size:15px}
.intro.note{font-size:13px;color:var(--mid);font-weight:500;text-transform:uppercase}
.field{border:1px solid var(--line);font-size:11px;color:#777;padding:14px 15px}
.captcha{left:485px;top:1736px;width:230px;height:57px;border:1px solid #d3d3d3;background:#f9f9f9;border-radius:3px;font-size:10px}
.captcha .box{position:absolute;left:11px;top:18px;width:20px;height:20px;border:2px solid #c1c1c1;background:#fff;border-radius:2px}
.captcha .lbl{position:absolute;left:40px;top:22px}
.captcha .brandlet{position:absolute;right:10px;top:34px;font-size:7px;color:#555;text-align:center;line-height:9px}
.captcha .brandlet::before{content:"";display:block;margin:0 auto 2px;width:18px;height:18px;border-radius:50%;border:3px solid var(--sky);position:absolute;top:-24px;left:8px}
.submit{left:540px;top:1811px;width:120px;height:42px;background:var(--cyan);color:#fff;font-weight:600;font-size:15px;text-align:center;line-height:42px;border-radius:2px}

/* footer */
.site-footer{left:0;top:1929px;width:1200px;height:527px;background:var(--navy);color:#fff}
.footer-brand{left:0;width:1200px;top:70px;text-align:center}
.footer-brand .name{font-size:44px;font-weight:600;letter-spacing:1px;line-height:46px}
.footer-brand .tag{font-size:14px;font-weight:500;margin-top:2px}
.footer-rule{left:162px;width:877px;height:1px;background:rgba(255,255,255,.2)}
.footer-nav a{position:absolute;top:229px;font-size:16px;color:#fff;text-decoration:none}
.footer-social{top:225px;width:30px;height:30px;border-radius:50%;background:#fff}
.footer-info{font-size:14px;line-height:24px}
.footer-info svg{position:absolute;left:-22px;top:3px}
.footer-info .hl{color:var(--cyan);font-weight:500}
.copyright{left:0;width:1200px;top:462px;text-align:center;font-size:13px}
.copyright b{font-weight:600}
</style>
</head>
<body>

<header class="abs site-header">
  <div class="abs brand"><span class="brand-mark"></span><span class="brand-name">Suds Haven</span></div>
  <div class="abs brand-tag">A FULL SERVICE LAUNDROMAT</div>
  <nav class="main-nav">
    <a style="left:529px">HOME</a>
    <a style="left:610px">ABOUT US</a>
    <a style="left:720px">SERVICES</a>
    <a style="left:824px">REVIEWS</a>
    <a class="active" style="left:925px">CONTACT US</a>
  </nav>
  <div class="abs nav-divider"></div>
  <span class="abs social-dot" style="left:1048px"></span>
  <span class="abs social-dot" style="left:1073px"></span>
</header>

<section class="abs hero">
  <div class="hero-photo" role="img" aria-label="Retro laundromat interior with rows of front-loading washers and a woman in a blue dress walking past"></div>
  <svg width="1200" height="600" viewBox="0 0 1200 600">
    <path d="M0,520 Q600,640 1200,515 L1200,600 L0,600 Z" fill="#fff"/>
    <path d="M0,530 Q580,650 1150,540 Q580,630 0,545 Z" fill="#0054aa"/>
  </svg>
</section>

<div class="abs breadcrumb">HOME / <span>CONTACT US</span></div>

<h1 class="abs section-title">CONTACT <b>US</b></h1>
<div class="abs title-rule"></div>

<section class="abs contact-panel">
  <div class="contact-row" style="top:57px">
    <svg width="20" height="22" viewBox="0 0 20 22" fill="none" stroke="#fff" stroke-width="1.2"><circle cx="10" cy="12" r="8"/><path d="M10 2c-3 3-3 17 0 18M2 12h16"/></svg>
    Brookfield Plaza Shopping Center,<br>2280 Maple Crest Ave NE., # 112,<br>Atlanta, GA 30399
  </div>
  <div class="contact-row" style="top:154px">
    <svg width="20" height="20" viewBox="0 0 20 20" fill="none" stroke="#fff" stroke-width="1.2"><path d="M4 2l3 0 2 5-2 2c1 2 3 4 5 5l2-2 5 2v3c-8 1-16-7-15-15z"/></svg>
    (404) 555-0142
  </div>
  <div class="contact-row" style="top:206px">
    <svg width="22" height="18" viewBox="0 0 22 18" fill="none" stroke="#fff" stroke-width="1.2"><rect x="1" y="2" width="20" height="14"/><path d="M1 2l10 8 10-8M1 16l7-7M21 16l-7-7"/></svg>
    hello@sudshavenatlanta-example.com
  </div>
  <div class="contact-row" style="top:258px">
    <svg width="22" height="22" viewBox="0 0 22 22" fill="none" stroke="#fff" stroke-width="1.2"><circle cx="11" cy="11" r="10"/><circle cx="11" cy="11" r="7"/><path d="M11 6v5l3 2"/></svg>
    Covid 19 hours<br>open 7 days a week 8 am to 8 pm
  </div>
</section>

<div class="abs map" role="img" aria-label="Street map of the surrounding neighbourhood with the laundromat location pinned"></div>
<div class="abs map-card">
  <h3>Suds Haven</h3>
  <p>2280 Maple Crest Ave NE #112,<br>Atlanta, GA 30399, United States</p>
  <div class="rating">4.7<i>★★★★★</i><a>156 reviews</a></div>
  <a class="more">View larger map</a>
</div>
<div class="abs map-zoom"><i></i></div>

<p class="abs intro" style="top:1451px">Would You Like To Know More About Us?</p>
<p class="abs intro" style="top:1486px">Have A Question About Our Services?</p>
<p class="abs intro note" style="top:1523px">Please feel free to call or email us for more information.</p>

<div class="abs field" style="left:337px;top:1563px;width:255px;height:42px">Name*</div>
<div class="abs field" style="left:607px;top:1563px;width:255px;height:42px">Email*</div>
<div class="abs field" style="left:337px;top:1621px;width:525px;height:94px">How may we help you?</div>

<div class="abs captcha">
  <span class="box"></span><span class="lbl">I'm not a robot</span>
  <span class="brandlet">Verify<br>Privacy · Terms</span>
</div>
<div class="abs submit">Submit</div>

<footer class="abs site-footer">
  <div class="abs footer-brand">
    <div class="name">SUDS HAVEN</div>
    <div class="tag">A FULL SERVICE LAUNDROMAT</div>
  </div>
  <div class="abs footer-rule" style="top:198px"></div>
  <nav class="footer-nav">
    <a style="left:291px">Home</a>
    <a style="left:378px">About Us</a>
    <a style="left:490px">Services</a>
    <a style="left:595px">Reviews</a>
    <a style="left:708px">Contact Us</a>
  </nav>
  <span class="abs footer-social" style="left:833px"></span>
  <span class="abs footer-social" style="left:878px"></span>
  <div class="abs footer-rule" style="top:280px"></div>

  <div class="abs footer-info" style="left:276px;top:306px">
    <svg width="18" height="20" viewBox="0 0 20 22" fill="none" stroke="#fff" stroke-width="1.2"><circle cx="10" cy="12" r="8"/><path d="M10 2c-3 3-3 17 0 18M2 12h16"/></svg>
    Brookfield Plaza Shopping Center, 2280 Maple<br>Crest Ave NE., # 112, Atlanta, GA 30399
  </div>
  <div class="abs footer-info" style="left:276px;top:360px">
    <svg width="18" height="18" viewBox="0 0 20 20" fill="none" stroke="#fff" stroke-width="1.2"><path d="M4 2l3 0 2 5-2 2c1 2 3 4 5 5l2-2 5 2v3c-8 1-16-7-15-15z"/></svg>
    (404) 555-0142
  </div>
  <div class="abs footer-info" style="left:611px;top:306px">
    <span class="hl">Delivery Available* please contact us for details</span><br>
    <span style="display:block;margin-top:9px">Covid 19 hours – open 7 days a week 8 am to 8 pm<br>Last wash begins 6:30 pm</span>
  </div>
  <div class="abs footer-rule" style="top:416px"></div>
  <p class="abs copyright">Copyright © 2021 <b>Suds Haven Atlanta</b>. All Rights Reserved.</p>
</footer>

</body>
</html>
```